Brightwhisker Botanicals: Extracts for Pets

We need a brochure to help market the products. Brightwhisker Botanicals makes Chinese Herbal Extracts for cats and dogs. We have three products to launch with. An allergy, calming, and pain formula. They are based on traditional Chinese Medicine Formulas that have been used for hundreds of years on humans and animals. I would like the logo (attached) and have one or two cat/dogs pictures. They can be any of the pics from my website. Each product should have a descrition of what it treats (can pull from website). The brochure can highlight its convient, effective, and a safe alternative. It has to include:

This statement has not been evaluated by the KVQ.
This product is not intended to diagnose, treat, cure,
or prevent any disease. Brightwhisker is not liable for any adverse effects.

I included a sample with some of the important info for the products - the desing does not have to be similar, just an example of the copy

*I would like the format to be in Illustrator, vector, so that I can change sizes if I need to without loosing any detail.

Target Market(s)

Pet Owners

Industry/Entity Type

Pet Care

Font styles to use
Other font styles liked:
• Universal (as logo)

Requirements
Must have
• Logo, Description of each products.
Nice to have
• Dog or cat picture

```html
<!DOCTYPE html>
<html lang="en">
<head>
<meta charset="utf-8">
<title>Brightwhisker Botanicals – Pet Care Flyer</title>
<link href="https://fonts.googleapis.com/css2?family=Lato:wght@400;700&display=swap" rel="stylesheet">
<style>
  :root {
    --mint: #dcefd9;
    --slate: #4b5b57;
    --slate-veil: rgba(75, 91, 87, 0.9);
    --leaf: #66c23f;
    --leaf-soft: #a9d67a;
    --grass-light: #8fdc5a;
    --grass-deep: #3f9a2a;
    --ring: #d7ecd0;
    --white: #ffffff;
  }
  * { margin: 0; padding: 0; box-sizing: border-box; }
  html, body {
    width: 992px;
    height: 1200px;
    overflow: hidden;
    background: var(--mint);
    font-family: "Lato", Arial, sans-serif;
  }
  .flyer {
    position: relative;
    width: 992px;
    height: 1200px;
    background: var(--mint);
  }
  .flyer-shapes {
    position: absolute;
    inset: 0;
  }
  .title-band {
    position: absolute;
    left: 0;
    top: 120px;
    width: 440px;
    height: 92px;
    background: var(--slate);
    color: var(--white);
    font-weight: 700;
    font-size: 54px;
    letter-spacing: 1px;
    line-height: 92px;
    padding-left: 48px;
  }
  .brand {
    position: absolute;
    right: 60px;
    top: 110px;
    display: flex;
    align-items: center;
    gap: 18px;
  }
  .brand-dot {
    width: 64px;
    height: 64px;
    border-radius: 50%;
    background: var(--leaf-soft);
  }
  .brand-name {
    font-weight: 400;
    font-size: 34px;
    line-height: 1.15;
    color: var(--leaf);
  }
  .tagline {
    position: absolute;
    left: 48px;
    top: 520px;
    color: var(--white);
    font-weight: 400;
    font-size: 46px;
    line-height: 58px;
    letter-spacing: 1px;
    text-transform: uppercase;
  }
  .tagline span { display: block; }
  .tagline span:nth-child(2) { padding-left: 22px; }
  .tagline span:nth-child(3) { padding-left: 44px; }
  .care-badge {
    position: absolute;
    left: 760px;
    top: 580px;
    width: 156px;
    height: 156px;
    border-radius: 50%;
    background: var(--slate);
    border: 9px solid var(--ring);
    display: flex;
    flex-direction: column;
    align-items: center;
    justify-content: center;
    color: var(--white);
    font-size: 30px;
    line-height: 34px;
    text-align: center;
  }
  .products {
    position: absolute;
    left: 48px;
    top: 870px;
    width: 896px;
    display: flex;
    gap: 22px;
  }
  .product {
    flex: 1;
    background: var(--slate-veil);
    border-top: 6px solid var(--leaf);
    padding: 18px 20px 20px;
    color: var(--white);
  }
  .product-name {
    font-size: 22px;
    font-weight: 700;
    letter-spacing: 0.5px;
    text-transform: uppercase;
    margin-bottom: 10px;
  }
  .product-text {
    font-size: 15px;
    line-height: 21px;
  }
  .footer-strip {
    position: absolute;
    left: 0;
    bottom: 0;
    width: 992px;
    height: 96px;
    background: var(--slate);
    color: var(--white);
    display: flex;
    align-items: center;
    justify-content: space-between;
    padding: 0 48px;
    gap: 32px;
  }
  .disclaimer {
    font-size: 13px;
    line-height: 18px;
    max-width: 560px;
  }
  .website {
    font-size: 20px;
    letter-spacing: 0.5px;
    white-space: nowrap;
  }
</style>
</head>
<body>
  <main class="flyer">
    <svg class="flyer-shapes" width="992" height="1200" viewBox="0 0 992 1200">
      <defs>
        <linearGradient id="grass" x1="0" y1="0" x2="0.4" y2="1">
          <stop offset="0" stop-color="#8fdc5a"/>
          <stop offset="0.6" stop-color="#5fbf3a"/>
          <stop offset="1" stop-color="#3f9a2a"/>
        </linearGradient>
      </defs>
      <polygon class="accent-stripe" points="0,440 992,300 992,330 0,470" fill="#66c23f"/>
      <polygon class="slogan-panel" points="0,470 992,330 992,560 0,860" fill="#4b5b57"/>
      <polygon class="pet-photo" role="img" aria-label="Photo of a puppy and a kitten resting together on green grass"
               points="0,860 992,560 992,1104 0,1104" fill="url(#grass)"/>
    </svg>

    <div class="title-band">PET CARE</div>

    <div class="brand">
      <div class="brand-dot"></div>
      <div class="brand-name">Brightwhisker<br>Botanicals</div>
    </div>

    <h1 class="tagline">
      <span>Take</span>
      <span>A good</span>
      <span>Care of pets</span>
    </h1>

    <div class="care-badge"><span>100%</span><span>CARE</span></div>

    <section class="products">
      <article class="product">
        <h2 class="product-name">Allergy Formula</h2>
        <p class="product-text">Soothes itchy skin, sneezing and seasonal allergies with a classic Chinese herbal blend.</p>
      </article>
      <article class="product">
        <h2 class="product-name">Calming Formula</h2>
        <p class="product-text">Eases anxiety, restlessness and stress from travel, storms or time alone.</p>
      </article>
      <article class="product">
        <h2 class="product-name">Pain Formula</h2>
        <p class="product-text">Supports stiff joints and everyday aches so your pet stays active and comfortable.</p>
      </article>
    </section>

    <footer class="footer-strip">
      <p class="disclaimer">This statement has not been evaluated by the KVQ. This product is not intended to diagnose, treat, cure, or prevent any disease. Brightwhisker is not liable for any adverse effects.</p>
      <p class="website">WEBSITE:&nbsp; www.brightwhiskerpets.com</p>
    </footer>
  </main>
</body>
</html>
```